Need a new company business card

I am looking for a new company business card. Front and back. With information on it as per below. Card should be professional. Yet clever. Simple. Modern design. Pim card, traditional size. OK with say, all black or all red backside.

Varnholt is an indie, bootstrapped magazine advancing the work of intersectional feminists busting their buts to create a just world through the power of enterprise and innovation.

Varnholt is the home and voice of entrepreneurial feminism and feminist innovators worldwide. Entrepreneurial feminists are people (of all genders) who see inequality as an innovation priority. They work to advance gender equity and/or who strive to integrate and practice feminist principles, pedagogy, values into their innovation and entrepreneurship work.
We are committed to this space being trans and queer inclusive, anti-racist, intersectional, brave, and safe. We welcome all allies. We value learning, edgy but civil discourse and integrative thinking skills.

Target Market(s)

feminists, business owners,

Industry/Entity Type

Publishing Company

Contact Information for Business Card

RD Tolliver
Founder/Publisher
4-237 Ashgrove Lane, Toronto, ON
M4T 2K8
publisher@varnholt.com
416-552-3019
www.varnholt.com

Font styles to use
Serif
Other font styles liked:
• Myriad Pro

Colors
ec1f27
000000
ffffff

Requirements
Must have
• logo
• use red, black white colours only.
Nice to have
• use the compass in pattern or creatively but not too busy please
Should not have
• Should not be too busy. Elegant.

```html
<!DOCTYPE html>
<html lang="en">
<head>
<meta charset="utf-8">
<title>Varnholt business card</title>
<link href="https://fonts.googleapis.com/css2?family=Source+Sans+3:wght@400;600;700&family=Cormorant+Garamond:wght@500&family=Roboto:wght@400;500;700&display=swap" rel="stylesheet">
<style>
  :root {
    --red: #ec1f27;
    --ink: #2b2b2b;
    --grey-text: #555555;
    --paper: #f3f3f3;
    --border-band: #c9c9c9;
    --back: #2d2d2d;
    --illustration: #4a4a4a;
    --stage: #ececec;
    --rule: #bdbdbd;
  }
  * { margin: 0; padding: 0; box-sizing: border-box; }
  html, body { width: 1200px; height: 1159px; overflow: hidden; }
  body { background: var(--stage); position: relative; font-family: "Source Sans 3", sans-serif; }

  .card { position: absolute; width: 700px; height: 400px; box-shadow: 0 6px 18px rgba(0,0,0,.12); overflow: hidden; }

  /* Front */
  .card-front { left: 250px; top: 100px; background: var(--border-band); }
  .card-front .pattern-border { position: absolute; inset: 0; background: var(--border-band); }
  .card-front .inner {
    position: absolute; inset: 28px; background: var(--paper);
    display: flex; align-items: center;
  }
  .brand { width: 330px; padding-left: 40px; }
  .brand-name {
    display: flex; align-items: center; gap: 10px;
    font-family: "Source Sans 3", sans-serif; font-weight: 700; font-size: 58px;
    color: var(--ink); letter-spacing: -1px; line-height: 1;
  }
  .brand-mark { width: 12px; height: 12px; background: var(--red); flex: none; }
  .tagline {
    margin-top: 8px; padding-left: 22px; white-space: nowrap;
    font-family: "Cormorant Garamond", serif; font-weight: 500; font-size: 10px;
    letter-spacing: 1.5px; text-transform: uppercase; color: var(--grey-text);
  }
  .divider { width: 1px; height: 190px; background: var(--rule); }
  .contact { padding-left: 34px; font-family: "Roboto", sans-serif; color: var(--grey-text); }
  .contact .person { font-weight: 700; font-size: 22px; color: var(--ink); }
  .contact .role { font-size: 16px; margin-top: 2px; }
  .contact .address { font-size: 15px; margin-top: 12px; line-height: 1.35; }
  .contact .lines { list-style: none; margin-top: 10px; font-size: 15px; line-height: 1.45; }
  .contact .lines li { display: flex; align-items: center; gap: 8px; }
  .contact .lines svg { width: 13px; height: 13px; flex: none; }

  /* Back */
  .card-back { left: 250px; top: 620px; background: var(--back); }
  .back-brand {
    position: absolute; left: 30px; top: 200px; width: 300px;
    transform-origin: 0 0; transform: rotate(-90deg) translate(-100px, 0);
  }
  .back-brand .brand-name { color: #ffffff; font-size: 50px; }
  .back-brand .tagline { color: #d8d8d8; font-size: 9px; padding-left: 20px; }
  .illustration-area {
    position: absolute; left: 150px; top: 40px; width: 510px; height: 320px;
    border-radius: 50%;
    background: radial-gradient(ellipse at center, #5a5a5a 0%, var(--illustration) 55%, var(--back) 100%);
  }
</style>
</head>
<body>
  <section class="card card-front">
    <div class="pattern-border" role="img" aria-label="Diagonal line pattern forming the card border"></div>
    <div class="inner">
      <div class="brand">
        <div class="brand-name"><span class="brand-mark"></span>Varnholt</div>
        <div class="tagline">Dispatches on enterprise and equity</div>
      </div>
      <div class="divider"></div>
      <div class="contact">
        <div class="person">RD Tolliver</div>
        <div class="role">Founder/Publisher</div>
        <div class="address">4-237 Ashgrove Lane<br>Toronto, ON, M4T 2K8</div>
        <ul class="lines">
          <li>
            <svg viewBox="0 0 16 16"><path d="M4 1l3 3-2 2c1 2 3 4 5 5l2-2 3 3-2 3C7 15 1 9 1 3z" fill="var(--red)"/></svg>
            416-552-3019
          </li>
          <li>
            <svg viewBox="0 0 16 16"><rect x="1" y="3" width="14" height="10" fill="none" stroke="var(--red)" stroke-width="1.5"/><path d="M1 3l7 6 7-6" fill="none" stroke="var(--red)" stroke-width="1.5"/></svg>
            publisher@varnholt.com
          </li>
          <li>
            <svg viewBox="0 0 16 16"><circle cx="8" cy="8" r="6.5" fill="none" stroke="var(--red)" stroke-width="1.5"/><ellipse cx="8" cy="8" rx="3" ry="6.5" fill="none" stroke="var(--red)" stroke-width="1.2"/><path d="M1.5 8h13" stroke="var(--red)" stroke-width="1.2"/></svg>
            www.varnholt.com
          </li>
        </ul>
      </div>
    </div>
  </section>

  <section class="card card-back">
    <div class="back-brand">
      <div class="brand-name"><span class="brand-mark"></span>Varnholt</div>
      <div class="tagline">Dispatches on enterprise and equity</div>
    </div>
    <div class="illustration-area" role="img" aria-label="White line illustration of a crowd of people and small shapes gathered around a central figure on black"></div>
  </section>
</body>
</html>
```